Quorva - corporate Business Card

We need a good look and innovative business card for a new start up company based in Los Angeles called "Quorva". We are in a payment business, including payment card, app, and ewallet. We are expert in online payment and Card not present (CNP) transaction.
We need an innovative, modern business card.

Our logo font is Aero Matics

Target Market(s)

Startup - Bank - Online Payment - Card Manufacturing

Industry/Entity Type

Startup

Contact Information for Business Card

phone: 555 014 7396 - Address: 4172 Marlowe blvd, Fernhollow, OR 97299

Requirements
Must have
• Message: innovative, professional, expert, high tech, trust, online payment expert, security
Nice to have
• no comment
Should not have
• no Comment

```html
<!DOCTYPE html>
<html lang="en">
<head>
<meta charset="utf-8">
<title>Quorva — Business Card</title>
<link rel="stylesheet" href="https://fonts.googleapis.com/css2?family=Exo+2:wght@600&family=Open+Sans:wght@400&display=swap">
<style>
  :root {
    --brand-red: #b91f2e;
    --card-white: #ffffff;
    --backdrop: #3b3532;
    --band-text: #ffffff;
  }
  * { margin: 0; padding: 0; box-sizing: border-box; }
  html, body {
    width: 1200px;
    height: 780px;
    overflow: hidden;
    background: var(--backdrop);
  }
  .canvas {
    position: relative;
    width: 1200px;
    height: 780px;
    display: flex;
    align-items: center;
    justify-content: center;
    gap: 60px;
  }
  .card {
    position: relative;
    width: 530px;
    height: 303px;
    background: var(--card-white);
    box-shadow: 0 12px 30px rgba(0, 0, 0, 0.45);
    overflow: hidden;
  }
  .brand {
    display: flex;
    align-items: center;
    gap: 10px;
    color: var(--brand-red);
    font-family: "Exo 2", sans-serif;
    font-weight: 600;
    letter-spacing: 1px;
    white-space: nowrap;
  }
  .brand-dot {
    flex: none;
    border-radius: 50%;
    background: var(--brand-red);
  }
  .card-front .brand {
    position: absolute;
    left: 50%;
    top: 50%;
    transform: translate(-50%, -50%);
    font-size: 58px;
  }
  .card-front .brand-dot { width: 62px; height: 62px; }

  .card-back .brand {
    position: absolute;
    left: 50%;
    top: 80px;
    transform: translateX(-50%);
    font-size: 52px;
  }
  .card-back .brand-dot { width: 56px; height: 56px; }

  .contact-band {
    position: absolute;
    left: 0;
    right: 0;
    bottom: 0;
    height: 122px;
    background: var(--brand-red);
    display: flex;
    flex-direction: column;
    align-items: center;
    justify-content: center;
    gap: 8px;
    color: var(--band-text);
    font-family: "Open Sans", sans-serif;
    font-size: 15px;
    white-space: nowrap;
  }
  .contact-phone {
    display: flex;
    align-items: center;
    gap: 6px;
  }
  .contact-phone svg { width: 15px; height: 15px; }
</style>
</head>
<body>
  <main class="canvas">
    <section class="card card-front" aria-label="Card front">
      <div class="brand">
        <span class="brand-dot" aria-hidden="true"></span>
        <span class="brand-name">Quorva</span>
      </div>
    </section>

    <section class="card card-back" aria-label="Card back">
      <div class="brand">
        <span class="brand-dot" aria-hidden="true"></span>
        <span class="brand-name">Quorva</span>
      </div>
      <div class="contact-band">
        <p class="contact-address">4172 Marlowe blvd, Fernhollow, OR 97299</p>
        <p class="contact-phone">
          <svg viewBox="0 0 16 16" aria-hidden="true">
            <circle cx="8" cy="8" r="8" fill="#ffffff"/>
            <path d="M5.2 4.2c.3-.2.7-.1.9.2l.8 1.3c.2.3.1.6-.1.8l-.5.4c.4.9 1.1 1.6 2 2l.4-.5c.2-.2.6-.3.8-.1l1.3.8c.3.2.4.6.2.9l-.4.7c-.3.4-.8.6-1.3.5C6.8 10.5 5.5 9.2 4.8 7.7c-.2-.5 0-1 .4-1.3z" fill="#b91f2e"/>
          </svg>
          555 014 7396
        </p>
      </div>
    </section>
  </main>
</body>
</html>
```